Business card design for holistic health care clinic

We need a double-sided business card design for our holistic health care clinic that integrates our logo design and also its color scheme. My business is called Valmira. It is an integrative medicine clinic. You have already done the logo for me. Please ensure an elegant and upscale design that is not cluttered, but still has all the necessary information (please see below for details).

Target Market(s)

Wellness, fitness, rehabilitation for educated, well-traveled open-minded clients who are focused on natural, organic, balanced and preventive healthcare and lifestyle.

Industry/Entity Type

Medical

Contact Information for Business Card

Modern, clean.

Number of Pages Required

1 page

Font styles to use
Serif
Sans Serif

Colors

Designer to choose colors to be used in the design.

Requirements
Must have
• Logo on one side, all other information on the other side.
• Other information should include:
• Tobias Wrenfeld - DOE, CPT, LMT
• 4100 East Marrow Drive
• Austin, TX 78119
• 512 555 0148
• 818 555 0192
• info@ValmiraHealth.example
• t.wrenfeld@ValmiraHealth.example
Nice to have
• Darker background on front - but not totally black - shaded/dark gray.

```html
<!DOCTYPE html>
<html lang="en">
<head>
<meta charset="utf-8">
<title>Valmira Business Card</title>
<link rel="stylesheet" href="https://fonts.googleapis.com/css2?family=Montserrat:wght@700&family=Work+Sans:wght@400&display=swap">
<style>
  :root {
    --page-bg: #e6e7e9;
    --card-dark: #2e2e30;
    --card-light: #ffffff;
    --brand-blue: #1a8fd1;
    --text-grey: #3b3b3d;
    --meta-grey: #6a6a6d;
  }
  * { box-sizing: border-box; margin: 0; padding: 0; }
  html, body {
    width: 1200px; height: 900px; overflow: hidden;
    background: var(--page-bg);
  }
  .canvas { position: relative; width: 1200px; height: 900px; }
  .card {
    position: absolute; left: 285px; width: 630px; height: 360px;
    overflow: hidden;
    box-shadow: 0 6px 18px rgba(0,0,0,0.18);
  }
  .card--front { top: 70px; background: var(--card-dark); }
  .card--back { top: 470px; background: var(--card-light); }

  .brand {
    position: absolute; display: flex; flex-direction: column; align-items: flex-start;
    white-space: nowrap;
  }
  .brand__name {
    font-family: "Montserrat", sans-serif; font-weight: 700;
    color: var(--brand-blue); line-height: 1; letter-spacing: 1px;
    display: flex; align-items: center; gap: 10px;
  }
  .brand__dot { display: inline-block; border-radius: 50%; background: var(--brand-blue); }
  .brand__tagline {
    font-family: "Montserrat", sans-serif; font-weight: 700;
    color: var(--brand-blue); margin-top: 8px;
  }
  .card--front .brand {
    left: 50%; top: 50%; transform: translate(-50%, -50%); align-items: center;
  }
  .card--front .brand__name { font-size: 66px; }
  .card--front .brand__dot { width: 18px; height: 18px; }
  .card--front .brand__tagline { font-size: 19px; }

  .card--back .brand { left: 36px; top: 132px; }
  .card--back .brand__name { font-size: 42px; }
  .card--back .brand__dot { width: 12px; height: 12px; }
  .card--back .brand__tagline { font-size: 13px; }

  .divider {
    position: absolute; left: 288px; top: 82px; width: 3px; height: 196px;
    background: var(--brand-blue);
  }
  .contact {
    position: absolute; left: 308px; top: 80px; width: 300px;
    font-family: "Work Sans", sans-serif; color: var(--text-grey);
    white-space: nowrap;
  }
  .contact__name {
    font-family: "Montserrat", sans-serif; font-weight: 700;
    color: var(--brand-blue); font-size: 22px; text-transform: uppercase;
    letter-spacing: 0.5px; margin-left: 6px; line-height: 1.1;
  }
  .contact__creds {
    font-size: 13px; color: var(--meta-grey); letter-spacing: 1px;
    margin: 4px 0 12px 6px;
  }
  .contact__address { font-size: 14px; line-height: 1.35; margin: 0 0 10px 6px; }
  .contact__list { list-style: none; font-size: 14px; }
  .contact__item { display: flex; align-items: center; gap: 9px; line-height: 1.5; }
  .contact__icon { width: 12px; height: 12px; flex: none; }
</style>
</head>
<body>
<main class="canvas">
  <section class="card card--front">
    <div class="brand">
      <div class="brand__name">Valmira<span class="brand__dot"></span></div>
      <div class="brand__tagline">Integrative Holistic Medicine</div>
    </div>
  </section>

  <section class="card card--back">
    <div class="brand">
      <div class="brand__name">Valmira<span class="brand__dot"></span></div>
      <div class="brand__tagline">Integrative Holistic Medicine</div>
    </div>
    <div class="divider"></div>
    <div class="contact">
      <div class="contact__name">Tobias Wrenfeld</div>
      <div class="contact__creds">DOE, CPT, LMT</div>
      <div class="contact__address">4100 East Marrow Drive<br>Austin, TX 78119</div>
      <ul class="contact__list">
        <li class="contact__item">
          <svg class="contact__icon" viewBox="0 0 16 16" fill="none" stroke="var(--brand-blue)" stroke-width="1.6"><path d="M4 1.5l2.5 3-1.5 1.5c.8 2 2.5 3.7 4.5 4.5l1.5-1.5 3 2.5-1.5 2.5C7 13.5 2.5 9 1.5 3z"/></svg>
          512 555 0148
        </li>
        <li class="contact__item">
          <svg class="contact__icon" viewBox="0 0 16 16" fill="none" stroke="var(--brand-blue)" stroke-width="1.6"><rect x="4" y="1" width="8" height="14" rx="1.5"/><line x1="7" y1="12.5" x2="9" y2="12.5"/></svg>
          818 555 0192
        </li>
        <li class="contact__item">
          <svg class="contact__icon" viewBox="0 0 16 16" fill="none" stroke="var(--brand-blue)" stroke-width="1.6"><rect x="1" y="3" width="14" height="10" rx="1"/><path d="M1.5 3.5L8 9l6.5-5.5"/></svg>
          info@ValmiraHealth.example
        </li>
        <li class="contact__item">
          <svg class="contact__icon" viewBox="0 0 16 16" fill="none" stroke="var(--brand-blue)" stroke-width="1.4"><circle cx="8" cy="8" r="6.5"/><ellipse cx="8" cy="8" rx="3" ry="6.5"/><line x1="1.5" y1="8" x2="14.5" y2="8"/></svg>
          t.wrenfeld@ValmiraHealth.example
        </li>
      </ul>
    </div>
  </section>
</main>
</body>
</html>
```